Looking for someone to design a business card for my plumbing business Quandor Plumbing Solutions I want the background also to be black, must attract clients. If possible I want the front to be the logo and the back to show maybe the details.

Target Market(s)

Clients

Industry/Entity Type

Plumbing maintenance

Contact Information for Business Card

Name: Felix, Contact: 0461 539 207, Email: quandorplumbingsolutions@mailbrook.example, Licence number 728093K

Font styles to use
Other font styles liked:
• as per logo maybe?

Colors

Designer to choose colors to be used in the design.

Requirements
Nice to have
• stating the service I provide, emergency plumbing, plumbing maintenance, drainage maintenance, block sewer and stormwater, camera and locating.

```html
<!DOCTYPE html>
<html lang="en">
<head>
<meta charset="utf-8">
<title>Quandor Plumbing Solutions – Business Card</title>
<link rel="stylesheet" href="https://fonts.googleapis.com/css2?family=Montserrat:wght@400;500;700;800&display=swap">
<style>
  :root {
    --page-bg: #141414;
    --card-bg: #222222;
    --accent-blue: #4a8fd0;
    --text-white: #f2f2f2;
    --text-soft: #e4e4e4;
  }
  * { margin: 0; padding: 0; box-sizing: border-box; }
  html, body {
    width: 1200px; height: 1059px; overflow: hidden;
    background: var(--page-bg);
    font-family: "Montserrat", sans-serif;
  }
  .canvas { position: relative; width: 1200px; height: 1059px; }
  .card {
    position: absolute;
    background: var(--card-bg);
    border-radius: 18px;
  }
  .card-details { left: 257px; top: 89px; width: 687px; height: 390px; }
  .card-front { left: 254px; top: 547px; width: 693px; height: 392px; }

  .brand-mark {
    position: absolute; left: 0; right: 0;
    display: flex; align-items: center; justify-content: center; gap: 12px;
    color: var(--text-white); font-weight: 800; text-transform: uppercase;
  }
  .brand-dot { border-radius: 50%; background: var(--accent-blue); flex: none; }
  .brand-name { display: flex; flex-direction: column; align-items: flex-start; line-height: 1; }
  .card-details .brand-mark { top: 66px; }
  .card-details .brand-dot { width: 30px; height: 30px; }
  .card-details .brand-primary { font-size: 38px; letter-spacing: 1px; }
  .card-details .brand-secondary { font-size: 15.5px; letter-spacing: 0.6px; margin-top: 5px; }
  .card-front .brand-mark { top: 150px; }
  .card-front .brand-dot { width: 52px; height: 52px; }
  .card-front .brand-primary { font-size: 64px; letter-spacing: 2px; }
  .card-front .brand-secondary { font-size: 25.5px; letter-spacing: 1px; margin-top: 8px; }

  .person {
    position: absolute; right: calc(687px - 268px); top: 216px;
    text-align: right; color: var(--text-soft);
  }
  .person-name { color: var(--accent-blue); font-weight: 700; font-size: 24px; line-height: 1.1; letter-spacing: 0.5px; }
  .person-role, .person-licence { font-size: 14.5px; line-height: 1.65; }

  .divider {
    position: absolute; left: 283px; top: 218px; width: 1.5px; height: 65px;
    background: var(--accent-blue);
  }
  .contact-list { position: absolute; left: 301px; top: 214px; list-style: none; }
  .contact-item {
    display: flex; align-items: center; gap: 7px;
    color: var(--text-soft); font-size: 14px; height: 26px;
  }
  .contact-icon { width: 13px; height: 13px; flex: none; }
  .social-dot { width: 12px; height: 12px; border-radius: 50%; background: var(--accent-blue); flex: none; }

  .services {
    position: absolute; left: 0; right: 0; top: 316px;
    text-align: center; color: var(--text-soft); font-size: 14.5px; line-height: 22px;
  }
  .services .sep { color: var(--accent-blue); margin: 0 8px; }
</style>
</head>
<body>
<main class="canvas">
  <section class="card card-details">
    <div class="brand-mark">
      <span class="brand-dot"></span>
      <span class="brand-name">
        <span class="brand-primary">Quandor</span>
        <span class="brand-secondary">Plumbing Solutions</span>
      </span>
    </div>

    <div class="person">
      <p class="person-name">FELIX</p>
      <p class="person-role">Founder &amp; CEO</p>
      <p class="person-licence">Licence number 728093K</p>
    </div>
    <div class="divider"></div>
    <ul class="contact-list">
      <li class="contact-item">
        <svg class="contact-icon" viewBox="0 0 24 24"><path fill="#4a8fd0" d="M6.6 10.8a15.1 15.1 0 0 0 6.6 6.6l2.2-2.2a1 1 0 0 1 1-.25 11.4 11.4 0 0 0 3.6.57 1 1 0 0 1 1 1V20a1 1 0 0 1-1 1A17 17 0 0 1 3 4a1 1 0 0 1 1-1h3.5a1 1 0 0 1 1 1c0 1.25.2 2.45.57 3.57a1 1 0 0 1-.25 1z"/></svg>
        <span>0461 539 207</span>
      </li>
      <li class="contact-item">
        <svg class="contact-icon" viewBox="0 0 24 24"><rect x="2" y="5" width="20" height="14" rx="1" fill="#4a8fd0"/><path d="M3 6l9 7 9-7" fill="none" stroke="#222" stroke-width="1.8"/></svg>
        <span>quandorplumbingsolutions@mailbrook.example</span>
      </li>
      <li class="contact-item">
        <span class="social-dot"></span>
        <span>@QuandorPlumbingSolutions</span>
      </li>
    </ul>

    <p class="services">
      Emergency plumbing<span class="sep">•</span>Plumbing maintenance<span class="sep">•</span>Drainage maintenance<br>
      Block sewer and stormwater<span class="sep">•</span>Camera and locating
    </p>
  </section>

  <section class="card card-front">
    <div class="brand-mark">
      <span class="brand-dot"></span>
      <span class="brand-name">
        <span class="brand-primary">Quandor</span>
        <span class="brand-secondary">Plumbing Solutions</span>
      </span>
    </div>
  </section>
</main>
</body>
</html>
```